Website Re-design

Hi, I'm looking for help in redesigning my web site. I currently have a site www.brightferncove.example where I sell lamps, and while I like some aspects of the design, you can tell that I have done the graphics myself and am not a pro at it. I'd like help in redesigning it, and am open to completely new design graphics. I have made the 3 slider images myself, and I feel they could be a bit better, but I am not sure how to do it. For example, on the homepage, the 'About Us', 'Secured Shopping', and '$10 Off' graphics don't go well with the rest of the page. I would like more cohesion in the design and more visual interest in the header, which is pretty basic right now. Also, that the bottom footer is black, I would like instead something else. I am looking for just the layout of the homepage, and possibly once that is done to work on more visual interest in some of the informational pages and product pages. I am looking for just the design in the form of a photoshop file or files that I can incorporate into my site. Thank you!
Updates

Project Deadline Extended
Reason: I just made this project payment committed, so I'd like a chance for designers who only choose payment committed projects to submit artwork. Thank you.

This project is now payment guaranteed/ committed.  Thanks.

Industry/Entity Type

Shopping

```html
<!DOCTYPE html>
<html lang="en">
<head>
<meta charset="utf-8">
<title>Bright Fern Cove — Lamps &amp; Lighting</title>
<link href="https://fonts.googleapis.com/css2?family=Lobster&family=Lora:ital@0;1&family=Open+Sans:wght@400;600;700&display=swap" rel="stylesheet">
<style>
  :root{
    --ink:#3a3a3a;
    --muted:#8a8a8a;
    --line:#e2e2e2;
    --page:#ffffff;
    --wash:#f3f3f3;
    --teal-deep:#1d6f78;
    --teal-mid:#3fa3a6;
    --teal-light:#8ccfcc;
    --wood:#cfc9bf;
    --orange:#e8521f;
    --blue:#3aa7c9;
    --red:#e0262d;
    --green:#7cbf4a;
    --social-a:#3b5998;
    --social-b:#38b3e6;
    --social-c:#cb2027;
  }
  *{box-sizing:border-box;margin:0;padding:0}
  html,body{width:784px;height:1200px;overflow:hidden}
  body{background:var(--page);font-family:"Open Sans",Arial,sans-serif;color:var(--ink);position:relative}

  .utility-bar{height:20px;display:flex;justify-content:flex-end;align-items:center;gap:14px;padding-right:58px;font-size:8px;color:var(--muted);border-bottom:1px solid var(--line)}
  .utility-bar b{color:var(--ink)}
  .search-box{width:80px;height:13px;border:1px solid var(--line);border-radius:2px;display:flex;justify-content:flex-end;align-items:center;padding-right:3px}

  .site-header{height:97px;position:relative}
  .brand{position:absolute;left:78px;top:26px;display:flex;align-items:center;gap:9px}
  .brand-mark{width:22px;height:22px;border-radius:50%;background:var(--ink)}
  .brand-name{font-size:20px;font-weight:600;color:var(--ink)}
  .cart-tools{position:absolute;right:58px;top:20px;display:flex;gap:8px;align-items:center;font-size:8px;color:var(--muted)}
  .cart-tools .btn{border:1px solid var(--line);padding:2px 6px;border-radius:2px;color:var(--ink);background:var(--wash)}
  .main-nav{position:absolute;right:58px;top:66px;display:flex;font-size:10px;font-weight:600}
  .main-nav a{color:var(--ink);text-decoration:none;padding:7px 14px;border-left:1px solid var(--line)}
  .main-nav a:first-child{border-left:none}

  .hero{position:absolute;top:117px;left:0;width:784px;height:418px;overflow:hidden}
  .hero-photo{position:absolute;inset:0;
    background:linear-gradient(to bottom,var(--teal-deep) 0%,var(--teal-mid) 35%,var(--teal-light) 62%,var(--wood) 78%,#bdb6ab 100%)}
  .hero-copy{position:absolute;left:118px;top:48px;width:250px;text-align:center;color:#fff}
  .hero-title{font-family:"Lobster",cursive;font-size:56px;line-height:.95}
  .hero-title small{display:block;font-size:28px}
  .hero-sub{font-family:"Lora",serif;font-size:16px;margin:16px 0 12px}
  .btn-shop{display:inline-block;background:var(--orange);color:#fff;font-family:"Lora",serif;font-size:15px;padding:7px 14px;border:2px solid #fff}
  .slider-dots{position:absolute;top:515px;left:0;width:100%;display:flex;justify-content:center;gap:5px}
  .slider-dots span{width:6px;height:6px;border-radius:50%;background:#fff;opacity:.6}
  .slider-dots span:first-child{opacity:1}

  .features{position:absolute;top:548px;left:99px;width:586px;display:flex;justify-content:space-between}
  .feature{width:164px;text-align:center}
  .feature-tab{height:62px;color:#fff;font-family:"Lobster",cursive;font-size:22px;display:flex;align-items:flex-end;justify-content:center;padding-bottom:9px;position:relative}
  .feature-icon{position:absolute;top:-18px;left:62px;width:40px;height:40px;border-radius:50%;border:2px solid #fff;display:flex;align-items:center;justify-content:center}
  .about .feature-tab,.about .feature-icon{background:var(--blue)}
  .secure .feature-tab,.secure .feature-icon{background:var(--red)}
  .offer .feature-tab,.offer .feature-icon{background:var(--green)}
  .feature p{font-size:8.5px;line-height:1.5;color:var(--ink);margin:10px 6px 10px}
  .feature .mini-btn{display:inline-block;font-size:6.5px;font-weight:700;color:#fff;padding:3px 8px;border-radius:2px}
  .about .mini-btn{background:var(--blue)} .secure .mini-btn{background:var(--red)} .offer .mini-btn{background:var(--green)}

  .products-title{position:absolute;top:722px;width:100%;text-align:center;font-family:"Lobster",cursive;font-size:26px;font-weight:400}
  .products-title::before,.products-title::after{content:"";display:inline-block;width:40px;height:1px;background:var(--line);vertical-align:middle;margin:0 12px}
  .carousel{position:absolute;top:770px;left:92px;width:600px;height:200px;display:flex;align-items:center;justify-content:space-between}
  .arrow{width:10px}
  .product-list{display:flex;gap:12px}
  .product{width:130px}
  .product-photo{height:150px;border:1px solid var(--line)}
  .product-name{font-size:7.5px;margin-top:5px}
  .product-price{font-size:7.5px;color:var(--orange)}
  .view-more{position:absolute;top:980px;left:352px;width:80px;text-align:center;font-size:7.5px;color:var(--muted);border:1px solid var(--line);border-radius:10px;padding:2px 0}

  .site-footer{position:absolute;top:1016px;left:0;width:784px;height:184px;background:var(--wash);border-top:1px solid var(--line)}
  .footer-cols{position:absolute;left:91px;top:18px;display:flex}
  .footer-col{width:104px;font-size:7.5px;line-height:1.75;color:var(--muted)}
  .footer-col h4{font-size:8px;color:var(--ink);font-weight:700;margin-bottom:2px}
  .signup{position:absolute;left:520px;top:18px;width:190px}
  .signup h4{font-size:8px;font-weight:700;margin-bottom:6px}
  .signup-form{display:flex}
  .signup-form span{flex:1;height:16px;border:1px solid var(--line);background:#fff;font-size:7px;color:var(--muted);padding:3px 4px}
  .signup-form b{background:var(--ink);color:#fff;font-size:7px;padding:3px 7px}
  .signup p{font-size:7px;color:var(--muted);margin:5px 0}
  .socials{display:flex;gap:6px}
  .socials span{width:20px;height:20px;border-radius:50%}
  .copyright{position:absolute;bottom:12px;width:100%;text-align:center;font-size:7px;color:var(--muted)}
</style>
</head>
<body>

<div class="utility-bar">
  <b>Sign in</b><span>Create account</span><span>My account</span>
  <span class="search-box"><svg width="7" height="7" viewBox="0 0 10 10"><circle cx="4" cy="4" r="3" fill="none" stroke="#8a8a8a" stroke-width="1.5"/><line x1="6.5" y1="6.5" x2="9.5" y2="9.5" stroke="#8a8a8a" stroke-width="1.5"/></svg></span>
</div>

<header class="site-header">
  <div class="brand"><span class="brand-mark"></span><span class="brand-name">Bright Fern Cove</span></div>
  <div class="cart-tools"><span class="btn">Shopping Cart</span><span>Wishlist</span><span class="btn">Checkout</span></div>
  <nav class="main-nav"><a href="#">HOME</a><a href="#">SHOP</a><a href="#">ABOUT US</a><a href="#">CONTACT US</a></nav>
</header>

<section class="hero">
  <div class="hero-photo" role="img" aria-label="Photo of a glass table lamp standing on a wooden floor against a teal wall"></div>
  <div class="hero-copy">
    <div class="hero-title">Light Up<small>the</small>Room</div>
    <div class="hero-sub">"The Marina" Medium Table Lamp</div>
    <span class="btn-shop">SHOP ALL LAMPS</span>
  </div>
</section>
<div class="slider-dots"><span></span><span></span><span></span></div>

<section class="features">
  <div class="feature about">
    <div class="feature-tab"><span class="feature-icon"><svg width="18" height="18" viewBox="0 0 20 20"><circle cx="10" cy="5" r="2" fill="#fff"/><rect x="8.5" y="8.5" width="3" height="9" fill="#fff"/></svg></span>About Us</div>
    <p>Bright Fern Cove provides beautiful and artistic home and hospitality lighting.</p>
    <span class="mini-btn">READ MORE</span>
  </div>
  <div class="feature secure">
    <div class="feature-tab"><span class="feature-icon"><svg width="18" height="18" viewBox="0 0 20 20"><path d="M6 9V6a4 4 0 0 1 8 0v3" fill="none" stroke="#fff" stroke-width="2"/><rect x="4" y="9" width="12" height="9" rx="1" fill="#fff"/></svg></span>Secured Shopping</div>
    <p>Shopping at Bright Fern Cove is secured and protected by industry standard best practices.</p>
    <span class="mini-btn">READ MORE</span>
  </div>
  <div class="feature offer">
    <div class="feature-tab"><span class="feature-icon"><svg width="18" height="18" viewBox="0 0 20 20"><path d="M2 10 10 2h8v8l-8 8z" fill="#fff"/><circle cx="14" cy="6" r="1.6" fill="#7cbf4a"/></svg></span>$10 Off</div>
    <p>$10 off any purchase when you sign up for our newsletter.</p>
    <span class="mini-btn">SIGN UP</span>
  </div>
</section>

<h2 class="products-title">Our Products</h2>
<section class="carousel">
  <svg class="arrow" viewBox="0 0 10 16"><path d="M8 2 2 8l6 6" fill="none" stroke="#8a8a8a" stroke-width="2"/></svg>
  <div class="product-list">
    <div class="product"><div class="product-photo" role="img" aria-label="Photo of a turquoise glass table lamp" style="background:linear-gradient(#f6f6f6,#bfe2e4)"></div><div class="product-name">Marina Medium Table Lamp</div><div class="product-price">$199.00</div></div>
    <div class="product"><div class="product-photo" role="img" aria-label="Photo of a purple glass table lamp" style="background:linear-gradient(#f6f6f6,#d6c4da)"></div><div class="product-name">Violet Arc Table Lamp</div><div class="product-price">$219.00</div></div>
    <div class="product"><div class="product-photo" role="img" aria-label="Photo of a patterned porcelain table lamp" style="background:linear-gradient(#f6f6f6,#e2d8ca)"></div><div class="product-name">Dune Porcelain Table Lamp</div><div class="product-price">$219.00</div></div>
    <div class="product"><div class="product-photo" role="img" aria-label="Photo of a sea-green glass table lamp" style="background:linear-gradient(#f6f6f6,#c4e2dc)"></div><div class="product-name">Tidewater Table Lamp</div><div class="product-price">$199.00</div></div>
  </div>
  <svg class="arrow" viewBox="0 0 10 16"><path d="M2 2l6 6-6 6" fill="none" stroke="#8a8a8a" stroke-width="2"/></svg>
</section>
<div class="view-more">View More</div>

<footer class="site-footer">
  <div class="footer-cols">
    <div class="footer-col"><h4>HELP + INFO</h4>Contact Us<br>Shipping Info<br>Returns<br>To The Trade<br>Privacy Policy<br>Terms of Use</div>
    <div class="footer-col"><h4>MY ACCOUNT</h4>Sign In<br>Order Status<br>Order History<br>Wish List<br>Checkout</div>
    <div class="footer-col"><h4>ABOUT</h4>Who We Are<br>Testimonials</div>
    <div class="footer-col"><h4>CONTACT</h4>Contact Us<br>hello@brightferncove.example</div>
  </div>
  <div class="signup">
    <h4>SIGN UP FOR BRIGHT FERN COVE EMAILS</h4>
    <div class="signup-form"><span>Enter email address</span><b>JOIN</b></div>
    <p>Receive your first savings this time at signup.</p>
    <div class="socials"><span style="background:var(--social-a)"></span><span style="background:var(--social-b)"></span><span style="background:var(--social-c)"></span></div>
  </div>
  <div class="copyright">© 2013 Bright Fern Cove. All Rights Reserved. · www.brightferncove.example</div>
</footer>

</body>
</html>
```